Stationery Set for Velmora Company

I need to create full stationery design for my company; Business Cards, Envelops, Letter Heads, Calendar.
In the letter head and Envelops... only contact information and website links.
Our company is a Service Management company with different domains of innovative services including Technology Service Management, Education Services, Outsourcing Management, Events Management.
I need a modern and innovative design specially for the business card. I some transparent designs and I like it, but don't limit your innovation to what I mentioned. Sky is limit for your innovation.

Target Market(s)

Middle East & Africa

Industry/Entity Type

Business Management

Colors
34a7d8
0355a3
85acd3
86cae7
cee9f5
cfdeed
e4daeb
f3f1f8
ecf7fb

Requirements
Must have
• Name, Title, Email, Mobile
Nice to have
• We have multiple locations in USA, KSA, EGY, so I need ideas about how to include all contact details maybe QR / Barcode or something else.
• Please see our locations and contact information: www.brightvelmora.example
Should not have
• Too much text

```html
<!DOCTYPE html>
<html lang="en">
<head>
<meta charset="utf-8">
<title>Velmora Company Business Card</title>
<link rel="stylesheet" href="https://fonts.googleapis.com/css2?family=Open+Sans:wght@400;600;700&display=swap">
<style>
  :root {
    --canvas: #e9e8e4;
    --card: #ffffff;
    --card-shade: #f1f1f1;
    --brand-blue: #3b66ae;
    --band-light: #6f93cc;
    --band-edge: #c9d6ea;
    --ink: #1e1e1e;
    --muted-ink: #2b2b2b;
  }
  * { margin: 0; padding: 0; box-sizing: border-box; }
  html, body {
    width: 1200px; height: 843px; overflow: hidden;
    background: var(--canvas);
    font-family: "Open Sans", Arial, sans-serif;
  }
  .sheet {
    width: 1200px; height: 843px;
    display: flex; align-items: center; justify-content: center; gap: 40px;
  }
  .card {
    position: relative;
    width: 560px; height: 320px;
    background: linear-gradient(160deg, var(--card) 55%, var(--card-shade));
    box-shadow: 0 10px 28px rgba(0,0,0,0.22);
    overflow: hidden;
  }
  .brand-name {
    position: absolute;
    width: 250px;
    color: var(--brand-blue);
    font-weight: 700;
    font-size: 22px;
    line-height: 28px;
    white-space: nowrap;
    display: flex; align-items: center; gap: 9px;
  }
  .brand-name .dot {
    width: 12px; height: 12px; background: var(--brand-blue); border-radius: 50%; flex: none;
  }
  /* back side */
  .card-back .brand-name { left: 36px; top: 140px; }
  .address-block {
    position: absolute; left: 320px; top: 40px;
    font-size: 14px; line-height: 18px; color: var(--muted-ink);
  }
  .address-block .region { color: var(--brand-blue); font-weight: 700; }
  /* front side */
  .card-front .brand-name { left: 36px; top: 92px; }
  .contact-block {
    position: absolute; left: 318px; top: 78px;
  }
  .person-name {
    color: var(--brand-blue); font-size: 19px; line-height: 24px; font-weight: 600; letter-spacing: 0.5px;
  }
  .person-title {
    color: var(--ink); font-size: 14px; line-height: 20px; font-weight: 600; margin-bottom: 10px;
  }
  .contact-line {
    display: flex; align-items: center; gap: 10px;
    font-size: 14px; line-height: 22px; color: var(--ink); white-space: nowrap;
  }
  .contact-line svg { width: 13px; height: 13px; flex: none; fill: var(--brand-blue); }
  .band {
    position: absolute; left: 0; right: 0; bottom: 0; height: 26px;
    background: linear-gradient(90deg, var(--brand-blue), var(--band-light) 50%, var(--brand-blue));
  }
  .band-edge {
    position: absolute; left: 0; right: 0; bottom: 26px; height: 3px;
    background: var(--band-edge);
  }
</style>
</head>
<body>
<main class="sheet">

  <section class="card card-back" aria-label="Business card back">
    <div class="brand-name"><span class="dot"></span>Velmora Company</div>
    <div class="address-block">
      <p class="region">USA:</p>
      <p>410 Harbor Crest Drive</p>
      <p>4th Floor Lakeview City</p>
      <p>CA 90000 US</p>
      <p class="region">Saudi Arabia:</p>
      <p>Al Noor District,</p>
      <p>Riyadh, Qasr Al Waha St.</p>
      <p>Nakheel Buildings</p>
      <p>3C 2nd Floor C12, C14</p>
    </div>
  </section>

  <section class="card card-front" aria-label="Business card front">
    <div class="brand-name"><span class="dot"></span>Velmora Company</div>
    <div class="contact-block">
      <p class="person-name">OMAR HADDAD</p>
      <p class="person-title">CEO/FOUNDER</p>
      <p class="contact-line">
        <svg viewBox="0 0 16 16"><path d="M3.5 1 6 3.5 4.6 5.5c.9 2.2 3.7 5 5.9 5.9L12.5 10 15 12.5 13 15C7 15 1 9 1 3z"/></svg>
        +1.5550102471 (USA)
      </p>
      <p class="contact-line">
        <svg viewBox="0 0 16 16"><path d="M3.5 1 6 3.5 4.6 5.5c.9 2.2 3.7 5 5.9 5.9L12.5 10 15 12.5 13 15C7 15 1 9 1 3z"/></svg>
        +966 90000 11 22 (Saudi)
      </p>
      <p class="contact-line">
        <svg viewBox="0 0 16 16"><path d="M4 0h8a1.5 1.5 0 0 1 1.5 1.5v13A1.5 1.5 0 0 1 12 16H4a1.5 1.5 0 0 1-1.5-1.5v-13A1.5 1.5 0 0 1 4 0zm0 2v10h8V2zm4 11a1 1 0 1 0 0 2 1 1 0 0 0 0-2z"/></svg>
        +1.5550102471
      </p>
      <p class="contact-line">
        <svg viewBox="0 0 16 16"><path d="M0 3h16v10H0zm1.5 1.5v.3L8 9l6.5-4.2v-.3z"/></svg>
        info@brightvelmora.example
      </p>
      <p class="contact-line">
        <svg viewBox="0 0 16 16"><path d="M8 0a8 8 0 1 0 0 16A8 8 0 0 0 8 0zm0 1.5c1 1.3 1.7 3.4 1.8 5.7H6.2C6.3 4.9 7 2.8 8 1.5zM1.6 8.8h3.1c.1 2 .6 3.9 1.4 5.2A6.5 6.5 0 0 1 1.6 8.8zm0-1.6A6.5 6.5 0 0 1 6.1 2c-.8 1.3-1.3 3.2-1.4 5.2zm4.6 1.6h3.6c-.1 2.3-.8 4.4-1.8 5.7-1-1.3-1.7-3.4-1.8-5.7zm5.1 0h3.1a6.5 6.5 0 0 1-4.5 5.2c.8-1.3 1.3-3.2 1.4-5.2zm0-1.6c-.1-2-.6-3.9-1.4-5.2a6.5 6.5 0 0 1 4.5 5.2z"/></svg>
        www.brightvelmora.example
      </p>
    </div>
    <div class="band-edge"></div>
    <div class="band"></div>
  </section>

</main>
</body>
</html>
```